Landing page for gamified shopping site

The target market for this Landing Page are Online sellers/merchants

Our website is www.Quorvex.com

Some background information on our site:
"Ready to make shopping more thrilling? With Quorvex, you can join a world of gamified shopping where players get the chance to win awesome products from their favorite brands - all for free! Compete with other customers in an exciting Dash 'n' Grab game and experience retail like never before. Plus, merchants are invited along too: promote your wares on our site and see what kind of wild success awaits!"

We now need a landing page that will target Online Sellers/Merchants. Please see content for this landing page attached.

This landing page will be comprised of 4 pages:
Home
How it Works
Case Studies
Why Free?
See PDF with content, which also breaks down the content in 4 sections.

The design of this landing page should not only look beautiful but also should be designed in a way that appeals to our target market (online merchants) who want to increase sales by showcasing their products on our website quorvex.com. So this landing page is the "bridge" between online merchants and our website Quorvex.com

The landing page design style should focus on clean and modern aesthetics that effectively communicate the intended message and drive conversions. It should also resemble our brand colors (see Quorvex.com)

If we are asked what look and feel we really, really like, here are two examples:

https://vend.brolimart.net/?ref_=hx_start_main

https://vend.brolimart.net/expand?initialSessionID=482-1173645-9081176&ld=XQSearch#label-enrol

What we like here is the choice of COLORS, FONTS & DESIGN ELEMENTS.

WE WOULD HIGHLY CONSIDER A DESIGN SIMILAR TO THIS WHICH IS CLEAN AND ELEGANT:

This is our logo:
https://files.tenvaro.net/folders/7kTqP2wLm9XzRbV4nHcYd3JfGs8UaE1oN?usp=sharing

This is the Quorvex virtual coin incase you want to incorporate it into the design:
https://files.tenvaro.net/file/d/4pWmXcN8rT2yLqZ_-VbKjHs6GdF3oA9eR/view?usp=sharing

We've also added to the attachments two screenshots that can inspire you for the image for the main banner of the site... showing a happy shopper/winner with products, indicating a fun game, fun shopping and winning products. For our image, we envision a very happy and excited shopper with perhaps the quorvex wheel behind the person and images of high-value products, conveying SHOPPING, GAME and WINNING.

Target Market(s)

Online Sellers/ Merchants

Industry/Entity Type

e-commerce

Number of Pages Required

4 page

Font styles to use
Other font styles liked:
• See fonts in this example: https://vend.brolimart.net/?ref_=hx_start_main

Colors

Designer to choose colors to be used in the design.

Requirements
Must have
• The landing page design style should focus on clean and modern aesthetics that effectively communicate the intended message and drive conversions. It should also resemble our brand colors (see Quorvex.com). We would seriously consider a design like this one which is nice and clean... https://vend.brolimart.net/expand?initialSessionID=482-1173645-9081176&ld=XQSearch#label-enrol
Nice to have
• A site that looks modern and beautiful but at the same time FUN and EXCITING. We really like the choice of COLORS, FONTS and DESIGN ELEMENTS used in this landing page: https://vend.brolimart.net/?ref_=hx_start_main

```html
<!DOCTYPE html>
<html lang="en">
<head>
<meta charset="utf-8">
<title>Quorvex — Free Store for Merchants</title>
<link href="https://fonts.googleapis.com/css2?family=Ubuntu:wght@400;500;700&family=Arimo:wght@400;700&display=swap" rel="stylesheet">
<style>
:root{
  --orange:#ff5a0a;
  --ink:#1b1f24;
  --text:#2a2e33;
  --sky:#e1eef3;
  --sky-soft:#f3f8fa;
  --card:#ffffff;
  --line:#eef1f3;
}
*{box-sizing:border-box;margin:0;padding:0}
html,body{width:1200px;height:2535px;overflow:hidden}
body{position:relative;background:#fff;font-family:"Arimo",Arial,sans-serif;color:var(--text)}
.abs{position:absolute}
.accent{color:var(--orange)}

/* header */
.site-header{position:absolute;left:0;top:0;width:1200px;height:90px;background:#fff}
.brand{position:absolute;left:60px;display:flex;flex-direction:column}
.brand-row{display:flex;align-items:center;gap:8px}
.brand-dot{width:22px;height:22px;border-radius:50%;background:var(--orange)}
.brand-name{font-family:"Ubuntu",sans-serif;font-weight:700;font-size:30px;color:var(--ink);letter-spacing:1px}
.brand-tag{font-family:"Ubuntu",sans-serif;font-size:9.5px;color:var(--ink);margin-top:2px}
.main-nav{position:absolute;right:60px;top:27px;display:flex;align-items:center;gap:29px;font-size:13px;color:var(--ink)}
.nav-cta{background:var(--orange);color:#fff;font-family:"Ubuntu",sans-serif;font-weight:700;padding:9px 15px;border-radius:18px;margin-left:-10px}

/* hero */
.hero{position:absolute;left:0;top:90px;width:1200px;height:840px;background:radial-gradient(ellipse at 50% 55%,#ffffff 0%,#f1f7fa 40%,var(--sky) 100%)}
.hero-wave{position:absolute;left:0;top:820px;width:1200px;height:120px}
.hero-kicker{position:absolute;top:154px;width:1200px;text-align:center;font-size:17px;color:var(--ink)}
.hero-title{position:absolute;top:196px;width:1200px;text-align:center;font-family:"Ubuntu",sans-serif;font-weight:700;font-size:38px;line-height:58.5px;color:var(--ink)}
.hero-copy{position:absolute;left:61px;top:408px;width:545px;font-size:14.6px;line-height:25.6px;color:var(--ink)}
.hero-copy p{margin-bottom:17px}
.btn{position:absolute;display:flex;align-items:center;justify-content:center;width:150px;height:45px;border-radius:23px;background:var(--orange);color:#fff;font-family:"Ubuntu",sans-serif;font-weight:700;font-size:16px;letter-spacing:.3px}
.mock{position:absolute;background:#fff;border-radius:14px;box-shadow:0 6px 24px rgba(40,80,100,.08)}
.mock-bar{position:absolute;left:18px;top:18px;right:18px;height:20px;display:flex;align-items:center;gap:14px}
.mock-bar i{display:block;height:6px;background:#dfe3e6;border-radius:3px}
.mock-visual{position:absolute;border-radius:8px}
.badge{position:absolute;border-radius:50%;background:#fff;border:2px solid var(--orange);display:flex;align-items:center;justify-content:center;text-align:center;font-family:"Ubuntu",sans-serif;font-weight:500;color:var(--ink)}

/* categories */
.section-title{position:absolute;width:1200px;text-align:center;font-family:"Ubuntu",sans-serif;font-weight:700;font-size:38px;color:var(--ink)}
.section-sub{position:absolute;width:1200px;text-align:center;font-size:14.6px;line-height:25.6px;color:var(--ink)}
.cat{position:absolute;width:158px;height:181px;background:var(--card);border-radius:10px;box-shadow:0 2px 10px rgba(0,0,0,.06);text-align:center}
.cat svg{position:absolute;left:50%;top:28px;transform:translateX(-50%);width:60px;height:60px;fill:none;stroke:var(--orange);stroke-width:2;stroke-linejoin:round;stroke-linecap:round}
.cat span{position:absolute;left:0;right:0;top:108px;font-family:"Ubuntu",sans-serif;font-size:16.5px;line-height:24px;color:var(--ink)}

/* promo */
.promo{position:absolute;left:0;top:1840px;width:1200px;height:530px;background:linear-gradient(90deg,#eef6f9 0%,#f6fafb 50%,var(--sky) 100%)}
.promo-title{position:absolute;left:60px;top:1988px;width:740px;font-family:"Ubuntu",sans-serif;font-weight:700;font-size:37px;line-height:47.5px;color:var(--ink)}
.promo-copy{position:absolute;left:62px;top:2146px;width:620px;font-size:14.6px;line-height:25.6px;color:var(--ink)}
.promo-photo{position:absolute;left:806px;top:1878px;width:334px;height:492px;border-radius:150px 150px 0 0;background:linear-gradient(180deg,#c98a62 0%,#d9443a 45%,#c92a2a 100%)}

/* footer */
.site-footer{position:absolute;left:0;top:2370px;width:1200px;height:165px;background:#fff}
.footer-nav{position:absolute;right:60px;top:2429px;display:flex;gap:29px;font-size:13px;color:var(--ink)}
.footer-nav .current{color:var(--orange)}
.copyright{position:absolute;right:60px;top:2460px;font-size:13px;color:var(--ink)}
</style>
</head>
<body>

<header class="site-header">
  <div class="brand" style="top:20px">
    <div class="brand-row"><span class="brand-dot"></span><span class="brand-name">Quorvex.com</span></div>
    <span class="brand-tag">Spin to win the brands you love — free</span>
  </div>
  <nav class="main-nav">
    <span>Home</span><span>How It Works</span><span>Case Studies</span><span class="nav-cta">Why Free?</span>
  </nav>
</header>

<section class="hero">
  <svg class="hero-wave" viewBox="0 0 1200 120" preserveAspectRatio="none">
    <path d="M0 0 H1200 V50 C1100 10 950 20 700 55 C450 90 200 110 0 80 Z" fill="#e6f1f5"/>
    <path d="M0 80 C200 110 450 90 700 55 C950 20 1100 10 1200 50 V120 H0 Z" fill="#fff"/>
  </svg>
</section>

<p class="hero-kicker">Are you ready to make a big splash in the online marketplace?</p>
<h1 class="hero-title">Get <span class="accent">12 months of FREE</span> unlimited campaigns<br>A <span class="accent">$2,388</span> value—plus a free store on Quorvex<br>Join our Beta-launch Today for <span class="accent">Explosive Growth</span></h1>

<div class="hero-copy">
  <p>Are you ready to take your brand to the next level? We are giving you an incredible opportunity with the Quorvex beta-launch program! Join us today and get 12 months of free unlimited campaigns, worth up to $2,38</p>
  <p>Plus, we'll set up a free store for you on our platform — at no cost. Not only that, but <span class="accent">you won't have to worry about transaction fees for a full year,</span> so all profits are yours alone. There's only 14 spots available, so don't hesitate; claim your store and become part of a supportive community where everyone is focused on helping each other succeed!</p>
  <p>Our expert team is here to provide their guidance and support every step of the way — just jump in now for an exciting journey culminating in exponential growth for your brand.</p>
</div>
<div class="btn" style="left:60px;top:748px">START NOW</div>

<div class="mock" style="left:765px;top:400px;width:375px;height:188px">
  <div class="mock-bar"><i style="width:40px"></i><i style="width:160px"></i><i style="width:50px;margin-left:auto"></i></div>
  <div class="mock-visual" role="img" aria-label="Velmora timepieces storefront banner with a wristwatch" style="left:18px;top:53px;width:338px;height:112px;background:linear-gradient(90deg,#6b3a2a 0%,#9a6656 40%,#e79aa8 75%,#f0a9b6 100%)"></div>
</div>
<div class="mock" style="left:685px;top:570px;width:376px;height:186px">
  <div class="mock-bar"><i style="width:40px"></i><i style="width:160px"></i></div>
  <div class="mock-visual" role="img" aria-label="Strideon sneaker storefront banner" style="left:18px;top:52px;width:338px;height:112px;background:linear-gradient(90deg,#3a3c42 0%,#2a1c1f 50%,#7a1a1e 80%,#c8242a 100%)"></div>
</div>
<div class="badge" style="left:955px;top:543px;width:140px;height:140px;font-size:16px;line-height:23px">
  <div><span class="accent">12 months</span><br>of Free<br>Unlimited<br>Campaigns</div>
</div>

<h2 class="section-title" style="top:980px">Eligible Store <span class="accent">Categories</span></h2>
<p class="section-sub" style="top:1042px">If your online store offers products in any one of these categories,&nbsp; your store may qualify<br>– and we’d love to hear from you:</p>

<!-- row 1 -->
<div class="cat" style="left:60px;top:1147px"><svg viewBox="0 0 60 60"><path d="M22 10 L12 16 L8 26 L16 28 L17 24 V52 H43 V24 L44 28 L52 26 L48 16 L38 10 C36 15 24 15 22 10Z"/></svg><span>Clothing</span></div>
<div class="cat" style="left:246px;top:1147px"><svg viewBox="0 0 60 60"><path d="M8 44 L14 30 C22 32 26 24 26 14 L34 14 C36 26 46 30 54 34 V44 H8Z M8 50 H54"/></svg><span>Shoes</span></div>
<div class="cat" style="left:430px;top:1147px"><svg viewBox="0 0 60 60"><path d="M6 30 H54 V46 H6Z M14 30 V10 M46 30 V10 M14 38 H46"/></svg><span>Consumer<br>Electronics</span></div>
<div class="cat" style="left:614px;top:1147px"><svg viewBox="0 0 60 60"><path d="M10 24 H28 V52 H10Z M14 24 V12 H24 V24 M32 32 H52 V52 H32Z"/><circle cx="42" cy="42" r="4"/></svg><span>Cosmetics &amp;<br>body care</span></div>
<div class="cat" style="left:800px;top:1147px"><svg viewBox="0 0 60 60"><path d="M12 32 C12 16 48 16 48 32 M10 30 H16 V42 H10Z M44 30 H50 V42 H44Z M20 34 H40 V46 H20Z M48 42 C48 52 38 54 32 54"/></svg><span>Books, movies,<br>music &amp; games</span></div>
<div class="cat" style="left:984px;top:1147px"><svg viewBox="0 0 60 60"><path d="M8 24 H40 V50 H8Z M16 24 C16 10 32 10 32 24 M36 30 H52 V50 H36Z"/></svg><span>Bags &amp;<br>accessories</span></div>

<!-- row 2 -->
<div class="cat" style="left:60px;top:1357px"><svg viewBox="0 0 60 60"><path d="M12 6 H48 V54 H12Z M12 16 H48"/><circle cx="30" cy="34" r="11"/></svg><span>Household<br>appliances</span></div>
<div class="cat" style="left:246px;top:1357px"><svg viewBox="0 0 60 60"><path d="M14 8 H30 C30 22 26 26 22 26 C18 26 14 22 14 8Z M22 26 V52 M14 52 H54 M32 44 H52 M34 44 C34 36 50 36 50 44"/></svg><span>Food &amp; drinks</span></div>
<div class="cat" style="left:430px;top:1357px"><svg viewBox="0 0 60 60"><path d="M16 30 V10 H44 V30 M8 30 H52 V46 H8Z M12 46 V52 M48 46 V52"/></svg><span>Furniture &amp;<br>household goods</span></div>
<div class="cat" style="left:614px;top:1357px"><svg viewBox="0 0 60 60"><path d="M48 6 L32 38 M8 42 C14 36 28 34 34 38 C30 48 18 52 8 42Z"/></svg><span>Sports &amp;<br>outdoor</span></div>
<div class="cat" style="left:800px;top:1357px"><svg viewBox="0 0 60 60"><circle cx="24" cy="20" r="10"/><circle cx="24" cy="40" r="12"/><path d="M40 54 V36 L48 28 L56 36 V54Z"/></svg><span>Toys &amp; baby<br>products</span></div>
<div class="cat" style="left:984px;top:1357px"><svg viewBox="0 0 60 60"><path d="M14 28 H46 L42 54 H18Z M22 28 L16 8 M30 28 V6 M38 28 L46 10"/></svg><span>Stationary &amp;<br>hobby supplies</span></div>

<!-- row 3 -->
<div class="cat" style="left:430px;top:1568px"><svg viewBox="0 0 60 60"><path d="M10 8 V22 C10 28 18 28 18 22 V8 M14 28 V52 M28 8 V52 M40 8 C50 14 50 28 40 30 V52"/></svg><span>DIY, garden<br>&amp; pets</span></div>
<div class="cat" style="left:614px;top:1568px"><svg viewBox="0 0 60 60"><path d="M14 16 H46 V52 H14Z M24 16 V8 H36 V16 M22 30 H38 V44 H22Z"/></svg><span>Vacations &amp;<br>travel</span></div>

<section class="promo">
  <svg class="abs" style="left:0;top:-10px" width="1200" height="110" viewBox="0 0 1200 110" preserveAspectRatio="none">
    <path d="M0 0 H1200 V20 C1000 0 750 30 500 70 C300 100 120 90 0 50Z" fill="#fff"/>
  </svg>
</section>
<div class="promo-photo" role="img" aria-label="Excited shopper in a red shirt giving a thumbs up"></div>
<div class="badge" style="left:747px;top:1927px;width:116px;height:116px;font-size:16px;line-height:22px">
  <div><span class="accent">0%</span><br>commission<br>on sales.</div>
</div>
<h2 class="promo-title">Your chance to dominate the Quorvex gamification platform, free—and <span class="accent">Take Part in a Revolutionary new way to shop!</span></h2>
<p class="promo-copy">Seize the chance to get your business off to a flying start – be one of our first fourteen stores to be included in our beta-launch and receive 12 months' full access – free of any charges, and 0% commission on sales.</p>
<div class="btn" style="left:60px;top:2245px">START NOW</div>

<footer class="site-footer">
  <div class="brand" style="top:28px">
    <div class="brand-row"><span class="brand-dot" style="width:26px;height:26px"></span><span class="brand-name" style="font-size:34px">Quorvex.com</span></div>
    <span class="brand-tag" style="font-size:10.5px">Spin to win the brands you love — free</span>
  </div>
</footer>
<nav class="footer-nav"><span class="current">Home</span><span>How It Works</span><span>Case Studies</span><span>Why Free?</span></nav>
<p class="copyright">©Quorvex.com - All rights reserved.</p>

</body>
</html>
```